Brintel Works - Fast, Efficient and Gas Mainteance for Domestic, Commercial and Industrial clients

We are in the process of purchasing a new business and would like to get a new logo and business card.
Business is a gas maintenance business that also does new gas installations.
Has been established since 1988.
Services include:
Install all types of gas appliances & equipment inc. hot water units
Maintain / repair / replace all types of gas appliances & equipment

Target Market(s)

Domestic, Commercial and Industrial clients

Industry/Entity Type

Business

Contact Information for Business Card

admin@brintelworks.com.au
07 3918 4726
Brintel Works PTY LTD

Logo Text

Gas Fitting & Plumbing Maintenance Specialists

Font styles to use
Sans Serif

Requirements
Must have
• Logo
• Business name, contact number, email address, web address
• Domestic | Commercial | Industrial Est Since 1988
Nice to have
• Possibly a black card with a flame logo to one side
Should not have
• Spelling errors

```html
<!DOCTYPE html>
<html lang="en">
<head>
<meta charset="utf-8">
<title>Brintel Works – Business Card</title>
<link rel="stylesheet" href="https://fonts.googleapis.com/css2?family=Noto+Serif:wght@400;700&family=Open+Sans:ital,wght@0,400;0,600;1,400&family=Yellowtail&display=swap">
<style>
  :root {
    --bg: #e9e6e1;
    --card-white: #f4f4f4;
    --card-black: #0d0d0d;
    --accent: #ec5a3e;
    --ink: #1c1c1c;
    --ink-soft: #55565c;
    --ink-muted: #8a8a8a;
    --on-dark: #d8d8d8;
  }
  * { box-sizing: border-box; margin: 0; padding: 0; }
  html, body { width: 1200px; height: 892px; overflow: hidden; }
  body {
    background: var(--bg);
    display: flex;
    align-items: center;
    justify-content: center;
    gap: 40px;
    font-family: "Open Sans", sans-serif;
  }
  .card {
    position: relative;
    width: 560px;
    height: 320px;
    border-radius: 4px;
    overflow: hidden;
    box-shadow: 0 6px 18px rgba(0,0,0,.25);
  }

  /* Front */
  .card--front { background: var(--card-white); }
  .front-band { position: absolute; inset: 0; }
  .brand { position: absolute; left: 30px; top: 34px; }
  .brand-name {
    font-family: "Noto Serif", serif;
    font-weight: 700;
    font-size: 32px;
    color: var(--accent);
    letter-spacing: .5px;
    line-height: 1;
  }
  .brand-name small {
    font-family: "Open Sans", sans-serif;
    font-size: 7px;
    color: var(--ink-soft);
    vertical-align: top;
    margin-left: 3px;
    letter-spacing: .5px;
  }
  .brand-tagline {
    font-weight: 600;
    font-size: 15px;
    color: var(--ink-soft);
    margin-top: 6px;
  }
  .brand-sectors {
    font-size: 8.5px;
    color: var(--ink-muted);
    margin-top: 3px;
  }
  .est {
    font-family: "Yellowtail", cursive;
    font-size: 15px;
    color: #a9a9a9;
    margin-left: 6px;
  }
  .contact {
    position: absolute;
    right: 22px;
    top: 34px;
    list-style: none;
    text-align: right;
  }
  .contact li {
    display: flex;
    align-items: center;
    justify-content: flex-end;
    gap: 10px;
    font-size: 14px;
    color: var(--ink);
    line-height: 24px;
  }
  .contact svg { width: 14px; height: 14px; flex: none; }
  .band-name {
    position: absolute;
    left: 46px;
    bottom: 48px;
    font-family: "Noto Serif", serif;
    font-weight: 700;
    font-size: 22px;
    color: var(--on-dark);
  }

  /* Back */
  .card--back {
    background: linear-gradient(160deg, #222 0%, var(--card-black) 45%, #050505 100%);
  }
  .back-lockup {
    position: absolute;
    left: 60px;
    top: 92px;
  }
  .back-name {
    font-family: "Noto Serif", serif;
    font-weight: 700;
    font-size: 46px;
    color: var(--accent);
    line-height: 1;
  }
  .back-name small {
    font-family: "Noto Serif", serif;
    font-size: 12px;
    color: var(--on-dark);
    margin-left: 8px;
    font-weight: 400;
    vertical-align: -6px;
  }
  .back-tagline {
    font-size: 16px;
    color: var(--on-dark);
    margin-top: 10px;
  }
  .back-sectors {
    font-size: 12px;
    color: var(--on-dark);
    margin-top: 4px;
  }
  .back-sectors .est { color: var(--on-dark); font-size: 17px; }
</style>
</head>
<body>

  <section class="card card--front" aria-label="Business card front">
    <svg class="front-band" viewBox="0 0 560 320" preserveAspectRatio="none" aria-hidden="true">
      <defs>
        <linearGradient id="band-sheen" x1="0" y1="0" x2="1" y2="1">
          <stop offset="0" stop-color="#2a2a2a"/>
          <stop offset=".5" stop-color="#0e0e0e"/>
          <stop offset="1" stop-color="#050505"/>
        </linearGradient>
      </defs>
      <path d="M0 170 C 120 150, 230 190, 330 260 C 360 282, 372 300, 380 320 L0 320 Z" fill="url(#band-sheen)"/>
    </svg>

    <div class="brand">
      <div class="brand-name">BRINTEL WORKS<small>PTY LTD</small></div>
      <div class="brand-tagline">Gas fitting &amp; Plumbing Specialists</div>
      <div class="brand-sectors">Domestic | Commercial | Industrial <span class="est">Est Since 1988</span></div>
    </div>

    <ul class="contact">
      <li>07 3918 4726
        <svg viewBox="0 0 14 14"><rect width="14" height="14" fill="#111"/><path d="M4 3.5l1.6-.5 1 2-1 .8a5 5 0 0 0 2.6 2.6l.8-1 2 1-.5 1.6C7 10.5 3.5 7 4 3.5z" fill="#fff"/></svg>
      </li>
      <li>07 3918 4727
        <svg viewBox="0 0 14 14"><rect width="14" height="14" fill="#111"/><rect x="3" y="5" width="8" height="5" fill="#fff"/><rect x="4.5" y="3" width="5" height="2" fill="#fff"/></svg>
      </li>
      <li>www.brintelworks.com.au
        <svg viewBox="0 0 14 14"><rect width="14" height="14" fill="#111"/><circle cx="7" cy="7" r="3.8" fill="none" stroke="#fff" stroke-width="1"/><path d="M3.2 7h7.6M7 3.2v7.6" stroke="#fff" stroke-width=".8"/></svg>
      </li>
      <li>admin@brintelworks.com.au
        <svg viewBox="0 0 14 14"><rect width="14" height="14" fill="#111"/><rect x="3" y="4" width="8" height="6" fill="#fff"/><path d="M3 4l4 3.5L11 4" fill="none" stroke="#111" stroke-width=".9"/></svg>
      </li>
      <li>PO Box 2864, Coral Point, QLD 4301
        <svg viewBox="0 0 14 14"><rect width="14" height="14" fill="#111"/><path d="M7 11.5S4 8.3 4 6a3 3 0 0 1 6 0c0 2.3-3 5.5-3 5.5z" fill="#fff"/><circle cx="7" cy="6" r="1" fill="#111"/></svg>
      </li>
    </ul>

    <div class="band-name">Brintel Works</div>
  </section>

  <section class="card card--back" aria-label="Business card back">
    <div class="back-lockup">
      <div class="back-name">Brintel Works<small>PTY LTD</small></div>
      <div class="back-tagline">Gas Fitting &amp; Plumbing Specialists</div>
      <div class="back-sectors">Domestic | Commercial | Industrial <span class="est">Est Since 1988</span></div>
    </div>
  </section>

</body>
</html>
```